BOLD & MINIMALIST DESIGN NEEDED

We want a very bold but minimalistic business card design that is impactful and utilizes both sides of the business card. Our current logo is included for your use.

We want bold fonts and good use of negative space. We don't want the logo to overpower the design.

Target Market(s)

Professionals who are building new commercial buildings.

Industry/Entity Type

Construction

Contact Information for Business Card

Name, Title, email, office phone, cell phone, website

Font styles to use
Serif
Sans Serif

Requirements
Must have
• Bold design!

```html
<!DOCTYPE html>
<html lang="en">
<head>
<meta charset="utf-8">
<title>Ridgeline Business Card</title>
<link rel="stylesheet" href="https://fonts.googleapis.com/css2?family=Poppins:wght@400;600;800&display=swap">
<style>
  :root {
    --backdrop: #6e5439;
    --card-dark: #0d0e10;
    --card-light: #ffffff;
    --ink: #111111;
    --accent: #7cc242;
    --paper-text: #ffffff;
    --frame-line: #1f2022;
  }
  * { box-sizing: border-box; margin: 0; padding: 0; }
  html, body {
    width: 1189px;
    height: 1200px;
    overflow: hidden;
    background: var(--backdrop);
    font-family: "Poppins", sans-serif;
  }
  .canvas { position: relative; width: 1189px; height: 1200px; }
  .card {
    position: absolute;
    left: 169px;
    width: 851px;
    height: 484px;
    border-radius: 34px;
    overflow: hidden;
    box-shadow: 0 10px 22px rgba(0,0,0,0.35);
  }
  .card--front { top: 112px; background: var(--card-dark); }
  .card--back { top: 641px; background: var(--card-light); }

  .brand {
    position: absolute;
    display: flex;
    align-items: center;
    gap: 14px;
    font-weight: 800;
    letter-spacing: 2px;
    line-height: 1;
  }
  .brand__mark { width: 26px; height: 26px; background: var(--accent); flex: none; }
  .card--front .brand {
    left: 0; right: 0; top: 218px;
    justify-content: center;
    font-size: 58px;
    color: var(--paper-text);
  }
  .card--back .brand {
    left: 58px; top: 272px;
    font-size: 50px;
    color: var(--ink);
  }
  .front-frame {
    position: absolute;
    left: 186px; top: 397px;
    width: 451px; height: 54px;
    border: 1px solid var(--frame-line);
  }

  .contact {
    position: absolute;
    left: 436px; top: 136px;
    color: var(--ink);
  }
  .contact__id {
    border-left: 3px solid var(--accent);
    padding-left: 20px;
    height: 46px;
  }
  .contact__name {
    font-weight: 600;
    font-size: 30px;
    line-height: 30px;
    margin-top: -6px;
  }
  .contact__title {
    font-size: 19px;
    line-height: 22px;
    color: var(--accent);
  }
  .contact__address {
    margin-top: 34px;
    font-size: 19.5px;
    line-height: 25px;
  }
  .contact__row {
    display: flex;
    align-items: center;
    gap: 16px;
    font-size: 21px;
    line-height: 28px;
  }
  .contact__row:first-of-type { margin-top: 14px; }
  .contact__icon { width: 16px; height: 16px; flex: none; }
</style>
</head>
<body>
<main class="canvas">
  <section class="card card--front" aria-label="Card front">
    <div class="brand"><span class="brand__mark"></span><span class="brand__name">RIDGELINE</span></div>
    <div class="front-frame"></div>
  </section>

  <section class="card card--back" aria-label="Card back">
    <div class="brand"><span class="brand__mark"></span><span class="brand__name">RIDGELINE</span></div>
    <div class="contact">
      <div class="contact__id">
        <p class="contact__name">MARCUS REED</p>
        <p class="contact__title">Craftsman</p>
      </div>
      <p class="contact__address">PO BOX 456 Harbour Road<br>4th Street Lakeside</p>
      <p class="contact__row">
        <svg class="contact__icon" viewBox="0 0 16 16" aria-hidden="true"><path fill="#7cc242" d="M4 1 L6.5 4.5 L5 6 C5.8 8.3 7.7 10.2 10 11 L11.5 9.5 L15 12 L13 15 C7 14 2 9 1 3 Z"/></svg>
        <span>(555) 010-2468</span>
      </p>
      <p class="contact__row">
        <svg class="contact__icon" viewBox="0 0 16 16" aria-hidden="true"><rect x="1" y="3" width="14" height="10" fill="#7cc242"/><path d="M1 3 L8 9 L15 3" stroke="#fff" stroke-width="1.4" fill="none"/></svg>
        <span>hello@ridgelinebuild.com</span>
      </p>
    </div>
  </section>
</main>
</body>
</html>
```